Realty Group Needs Classy, Contemporary Letterhead Design

We need a letterhead design for a new realty company located in NY, USA. We buy investment properties to rehabilitate and or keep in our rental portfolio.

```html
<!DOCTYPE html>
<html lang="en">
<head>
<meta charset="utf-8">
<title>Meridian Realty Group, LLC — Letterhead</title>
<link rel="stylesheet" href="https://fonts.googleapis.com/css2?family=Lato:wght@400;900&family=Arimo:wght@400&display=swap">
<style>
  :root {
    --brand-purple: #4b2a8a;
    --ink: #2f2f2f;
    --ink-soft: #444;
    --rule-grey: #8a8a8a;
    --backdrop: #dcdcdc;
    --paper: #ffffff;
  }
  * { box-sizing: border-box; margin: 0; padding: 0; }
  html, body {
    width: 1077px; height: 1200px; overflow: hidden;
    background: var(--backdrop);
  }
  .letterhead {
    position: absolute; left: 114px; top: 0;
    width: 848px; height: 1200px;
    background: var(--paper);
    font-family: "Lato", sans-serif;
    color: var(--ink);
  }
  .brand {
    position: absolute; left: 53px; top: 80px;
    width: 346px; text-align: center;
    color: var(--brand-purple);
    font-family: "Lato", sans-serif; font-weight: 900;
  }
  .brand-name { font-size: 60px; line-height: 64px; letter-spacing: -1px; }
  .brand-sub { font-size: 18px; line-height: 22px; letter-spacing: 1.5px; }
  .header-divider {
    position: absolute; left: 537px; top: 65px;
    width: 2px; height: 102px; background: var(--rule-grey);
  }
  .contact {
    position: absolute; left: 566px; top: 60px;
    font-family: "Arimo", sans-serif; font-size: 16.5px; font-style: normal;
    color: var(--ink-soft); line-height: 20.5px;
  }
  .contact-address { margin-bottom: 4px; }
  .contact-row { display: flex; align-items: center; gap: 6px; line-height: 22px; }
  .contact-row svg { width: 14px; height: 14px; fill: var(--brand-purple); flex: none; }
  .recipient {
    position: absolute; left: 53px; top: 294px;
    font-size: 15.5px; line-height: 21.4px; color: var(--ink-soft);
  }
  .letter-body {
    position: absolute; left: 53px; top: 392px; width: 749px;
    font-size: 15.5px; line-height: 24.3px; letter-spacing: 0.22px;
    text-align: justify; hyphens: auto; -webkit-hyphens: auto;
    color: var(--ink);
  }
  .letter-body p { margin-bottom: 21px; }
  .letter-body p.lead { padding-left: 8px; margin-bottom: 26px; }
  .closing {
    position: absolute; left: 53px; top: 796px;
    font-size: 16.5px; color: var(--ink);
  }
  .signature-area {
    position: absolute; left: 53px; top: 832px;
    width: 152px; height: 62px;
    background: linear-gradient(90deg, #f1f1f1, #e6e6e6);
  }
  .footer { position: absolute; left: 0; bottom: 0; width: 848px; height: 45px; }
  .footer > svg { position: absolute; left: 0; top: 0; }
  .footer-web {
    position: absolute; left: 449px; width: 313px; top: 7px;
    display: flex; align-items: center; justify-content: center; gap: 6px;
    font-family: "Arimo", sans-serif; font-size: 16px; color: #fff;
  }
  .footer-web svg { width: 13px; height: 13px; fill: #fff; }
</style>
</head>
<body>
<main class="letterhead">
  <header>
    <div class="brand">
      <div class="brand-name">MERIDIAN</div>
      <div class="brand-sub">Realty Group, LLC</div>
    </div>
    <div class="header-divider"></div>
    <address class="contact">
      <div class="contact-address">2480 W. Harbor Lane, Suite<br>310 Kingston, NY, USA</div>
      <div class="contact-row">
        <svg viewBox="0 0 24 24" aria-hidden="true"><path d="M6.6 10.8c1.4 2.8 3.8 5.1 6.6 6.6l2.2-2.2c.3-.3.7-.4 1-.2 1.1.4 2.3.6 3.6.6.6 0 1 .4 1 1V20c0 .6-.4 1-1 1C10.6 21 3 13.4 3 4c0-.6.4-1 1-1h3.5c.6 0 1 .4 1 1 0 1.3.2 2.5.6 3.6.1.3 0 .7-.2 1L6.6 10.8z"/></svg>
        <span>555-201-7734</span>
      </div>
      <div class="contact-row">
        <svg viewBox="0 0 24 24" aria-hidden="true"><path d="M6 3h12v5H6zM4 9h16a2 2 0 0 1 2 2v6h-4v4H6v-4H2v-6a2 2 0 0 1 2-2zm4 7v3h8v-3z"/></svg>
        <span>555-201-7790</span>
      </div>
      <div class="contact-row">
        <svg viewBox="0 0 24 24" aria-hidden="true"><path d="M2 5h20v14H2zm2 2v.5l8 5 8-5V7zm0 3v7h16v-7l-8 5z"/></svg>
        <span>hello@meridianrealtyllc.com</span>
      </div>
    </address>
  </header>

  <section class="recipient">
    Mr/s<br>First Name and Last Name<br>Company Name<br>Address
  </section>

  <section class="letter-body">
    <p class="lead">Lorem Ipsum is simply dummy text of the printing and typesetting industry. Lorem Ipsum has been the industry's standard dummy text ever since the 1500s, when an unknown printer took a galley of type and scrambled it to make a type specimen book. It has survived not only five centuries, but also the leap into electronic typesetting, remaining essentially unchanged. It was popularised in the 1960s with the release of Glyphora sheets containing Lorem Ipsum passages.</p>
    <p>he standard chunk of Lorem Ipsum used since the 1500s is reproduced below for those interested. Sections 1.10.32 and 1.10.33 from "de Ordine Litterarum Antiquarum" by Aulus Verenus are also reproduced in their exact original form, accompanied by English versions from the 1914 translation by T. Wardell. Lorem ipsum dolor sit amet, consectetur adipiscing elit, sed do eiusmod tempor incididunt ut labore et dolore magna aliqua.</p>
    <p>It is a long established fact that a reader will be distracted by the readable content of a page when looking at its layout. The point of using Lorem Ipsum is that it has a more-or-less normal distribution of letters, as opposed to using 'Content here, content here', making it look like readable English. Many desktop publishing packages and web page editors now .</p>
  </section>

  <div class="closing">Your Sincerely,</div>
  <div class="signature-area" role="img" aria-label="Handwritten signature"></div>

  <footer class="footer">
    <svg width="848" height="45" viewBox="0 0 848 45" aria-hidden="true">
      <rect x="0" y="30" width="848" height="15" fill="var(--rule-grey)"/>
      <polygon points="436,0 775,0 820,45 394,45" fill="var(--paper)"/>
      <polygon points="449,0 762,0 792,45 408,45" fill="var(--brand-purple)"/>
    </svg>
    <div class="footer-web">
      <svg viewBox="0 0 24 24" aria-hidden="true"><path d="M12 2a10 10 0 1 0 0 20 10 10 0 0 0 0-20zm-1 17.9A8 8 0 0 1 4.1 10L9 15v1a2 2 0 0 0 2 2zm6.9-2.5A2 2 0 0 0 16 16h-1v-3a1 1 0 0 0-1-1H8v-2h2a1 1 0 0 0 1-1V7h2a2 2 0 0 0 2-2v-.4a8 8 0 0 1 2.9 12.8z"/></svg>
      <span>www.meridianrealtyllc.com</span>
    </div>
  </footer>
</main>
</body>
</html>
```